Business Card for brovaLINK

Create a Business Card with an existing logo for brovaLINK AG. We are a Information Technology company that does consulting and developing SW to automate business processes. The main colors are given from the logo.

Industry/Entity Type

Business

Requirements
Nice to have
• we use a a font style Century Gothic in our documents

```html
<!DOCTYPE html>
<html lang="en">
<head>
<meta charset="utf-8">
<title>brovaLINK – Business Card</title>
<link rel="stylesheet" href="https://fonts.googleapis.com/css2?family=Questrial&family=Poppins:wght@600&display=swap">
<style>
  :root {
    --canvas: #e9e7e3;
    --card: #ffffff;
    --ink: #3a3d42;
    --ink-soft: #55595f;
    --blue: #1f6fc1;
    --blue-deep: #1a4fa0;
    --blue-light: #5fb4e8;
    --green: #3fae3a;
    --green-light: #a6d93a;
    --shadow: 0 18px 40px rgba(40, 35, 25, 0.22);
  }
  * { box-sizing: border-box; margin: 0; padding: 0; }
  html, body { width: 1200px; height: 1024px; overflow: hidden; }
  body {
    background: var(--canvas);
    font-family: "Questrial", "Century Gothic", sans-serif;
    color: var(--ink);
    position: relative;
  }
  .card {
    position: absolute;
    width: 600px;
    height: 388px;
    background: var(--card);
    border-radius: 22px;
    box-shadow: var(--shadow);
    overflow: hidden;
  }
  .card-front { left: 80px; top: 110px; }
  .card-back  { left: 520px; top: 530px; }
  .card svg.decor { position: absolute; inset: 0; width: 100%; height: 100%; }

  .brand-name {
    position: absolute;
    font-family: "Poppins", sans-serif;
    font-weight: 600;
    font-size: 34px;
    color: var(--blue-deep);
    line-height: 1;
    white-space: nowrap;
  }
  .card-front .brand-name { left: 44px; top: 62px; }
  .card-back .brand-name { left: 190px; top: 176px; }

  .person { position: absolute; left: 44px; top: 170px; }
  .person-name {
    font-family: "Poppins", sans-serif;
    font-weight: 600;
    font-size: 23px;
    color: var(--blue);
    line-height: 1.1;
  }
  .person-role {
    font-family: "Poppins", sans-serif;
    font-weight: 600;
    font-size: 16px;
    color: var(--green);
    margin-top: 2px;
  }
  .contact-list {
    position: absolute;
    left: 44px; top: 240px;
    list-style: none;
    font-size: 16px;
    color: var(--ink-soft);
    line-height: 25px;
  }
  .contact-list li { display: flex; align-items: center; gap: 10px; }
  .contact-list svg { width: 13px; height: 13px; fill: var(--blue); flex: none; }

  .web-vertical {
    position: absolute;
    right: 6px; top: 22px;
    writing-mode: vertical-rl;
    font-size: 14px;
    color: #ffffff;
    letter-spacing: 0.5px;
  }

  .web-back {
    position: absolute;
    left: 40px; bottom: 34px;
    font-size: 17px;
    color: var(--ink-soft);
  }
  .web-back .accent { color: var(--green); }
</style>
</head>
<body>

  <section class="card card-front" aria-label="Business card front">
    <svg class="decor" viewBox="0 0 600 388" preserveAspectRatio="none" aria-hidden="true">
      <defs>
        <linearGradient id="band-blue" x1="0" y1="0" x2="0" y2="1">
          <stop offset="0" stop-color="#5fb4e8"/>
          <stop offset="1" stop-color="#1a4fa0"/>
        </linearGradient>
      </defs>
      <path d="M562 0 H600 V388 H574 V230 L562 210 Z" fill="url(#band-blue)"/>
      <path d="M554 0 V212 L566 232 V388" fill="none" stroke="#3fae3a" stroke-width="4"/>
    </svg>

    <p class="brand-name">brovaLINK</p>

    <div class="person">
      <p class="person-name">Lukas Brenner</p>
      <p class="person-role">CEO</p>
    </div>

    <ul class="contact-list">
      <li><svg viewBox="0 0 16 16"><rect x="1" y="5" width="14" height="10" rx="2"/><rect x="4" y="1" width="8" height="5" rx="1"/></svg>+41 56 210 48 90</li>
      <li><svg viewBox="0 0 16 16"><path d="M3 1l3 1 1 4-2 1c1 2 2 3 4 4l1-2 4 1 1 3-2 2C7 15 1 9 1 3z"/></svg>+41 79 305 62 17</li>
      <li><svg viewBox="0 0 16 16"><path d="M1 3h14v10H1z M1 3l7 6 7-6" stroke="#fff" stroke-width="1"/></svg>lukas.brenner@brovalink.ch</li>
      <li><svg viewBox="0 0 16 16"><path d="M8 1a5 5 0 0 1 5 5c0 4-5 9-5 9S3 10 3 6a5 5 0 0 1 5-5zm0 3a2 2 0 1 0 0 4 2 2 0 0 0 0-4z"/></svg>Lindenweg 8, 5430 Talwil, Switzerland</li>
    </ul>

    <p class="web-vertical">www.brovalink.ch</p>
  </section>

  <section class="card card-back" aria-label="Business card back">
    <svg class="decor" viewBox="0 0 600 388" preserveAspectRatio="none" aria-hidden="true">
      <defs>
        <linearGradient id="wave-blue" x1="0" y1="0" x2="1" y2="1">
          <stop offset="0" stop-color="#5fb4e8"/>
          <stop offset="1" stop-color="#d9ecf8"/>
        </linearGradient>
        <linearGradient id="wave-green" x1="0" y1="0" x2="1" y2="1">
          <stop offset="0" stop-color="#e6f6b8"/>
          <stop offset="1" stop-color="#a6d93a"/>
        </linearGradient>
        <linearGradient id="paper" x1="0" y1="0" x2="0" y2="1">
          <stop offset="0" stop-color="#ffffff"/>
          <stop offset="1" stop-color="#eceef0"/>
        </linearGradient>
      </defs>
      <rect width="600" height="388" fill="url(#paper)"/>
      <path d="M0 0 H170 C120 30 60 80 0 140 Z" fill="url(#wave-blue)"/>
      <path d="M600 160 C470 200 330 290 250 388 H600 Z" fill="#3fae3a"/>
      <path d="M600 178 C480 220 360 300 290 388 H600 Z" fill="url(#wave-green)"/>
    </svg>

    <p class="brand-name">brovaLINK</p>

    <p class="web-back">www.<span class="accent">brovalink</span>.ch</p>
  </section>

</body>
</html>
```